Accounting firm needing business card / letterhead designed
Marcus L. Trenholm, CPA
marcus@veltrowledger.com
www.veltrowledger.com
842 E Alder Ave Brinmoor, KS 43827
555-562-0974

```html
<!DOCTYPE html>
<html lang="en">
<head>
<meta charset="utf-8">
<title>Veltrow Ledger – Business Card</title>
<link rel="stylesheet" href="https://fonts.googleapis.com/css2?family=Michroma&family=Orbitron:wght@700&family=Roboto:wght@400&display=swap">
<style>
  :root {
    --bg: #e6e6e6;
    --green: #8dc63f;
    --navy: #27235f;
    --white: #ffffff;
    --card-white: #f6f6f6;
    --text-grey: #555555;
  }
  * { margin: 0; padding: 0; box-sizing: border-box; }
  html, body {
    width: 1200px;
    height: 960px;
    overflow: hidden;
    background: var(--bg);
  }
  .canvas {
    position: relative;
    width: 1200px;
    height: 960px;
  }
  .card {
    position: absolute;
    left: 320px;
    width: 600px;
    height: 342px;
    border-radius: 22px;
    overflow: hidden;
  }
  /* Front */
  .card-front {
    top: 108px;
    background: var(--green);
  }
  .card-front .brand-name {
    position: absolute;
    left: 0;
    right: 0;
    top: 150px;
    text-align: center;
    font-family: "Michroma", sans-serif;
    font-size: 32px;
    letter-spacing: 2px;
    color: var(--navy);
  }
  .card-front .website {
    position: absolute;
    left: 0;
    right: 0;
    top: 280px;
    text-align: center;
    font-family: "Roboto", sans-serif;
    font-size: 15px;
    letter-spacing: 6.5px;
    color: var(--white);
  }
  /* Back */
  .card-back {
    top: 493px;
    background: var(--card-white);
  }
  .card-back .accent-green {
    position: absolute;
    left: 0;
    top: 32px;
    width: 18px;
    height: 93px;
    background: var(--green);
  }
  .card-back .brand-name {
    position: absolute;
    left: 38px;
    top: 62px;
    font-family: "Michroma", sans-serif;
    font-size: 28px;
    letter-spacing: 1.5px;
    color: var(--navy);
  }
  .card-back .accent-navy {
    position: absolute;
    right: 0;
    top: 200px;
    width: 15px;
    height: 109px;
    background: var(--navy);
  }
  .contact {
    position: absolute;
    right: 25px;
    top: 198px;
    text-align: right;
    font-family: "Roboto", sans-serif;
    color: var(--text-grey);
  }
  .contact .person {
    font-family: "Orbitron", sans-serif;
    font-weight: 700;
    font-size: 16px;
    letter-spacing: 1px;
    color: var(--navy);
    margin-bottom: 10px;
  }
  .contact .address {
    font-size: 14.5px;
    margin-bottom: 10px;
  }
  .contact .line {
    display: flex;
    justify-content: flex-end;
    align-items: center;
    gap: 7px;
    font-size: 14.5px;
    line-height: 19px;
  }
  .contact .icon {
    width: 13px;
    height: 13px;
    fill: var(--navy);
  }
</style>
</head>
<body>
<div class="canvas">

  <section class="card card-front">
    <div class="brand-name">VELTROW LEDGER</div>
    <div class="website">www.veltrowledger.com</div>
  </section>

  <section class="card card-back">
    <div class="accent-green"></div>
    <div class="brand-name">VELTROW LEDGER</div>
    <div class="accent-navy"></div>
    <div class="contact">
      <div class="person">MARCUS L. TRENHOLM, CPA</div>
      <div class="address">842 E Alder Ave, Brinmoor, KS 43827</div>
      <div class="line">555-562-0974
        <svg class="icon" viewBox="0 0 24 24" aria-hidden="true"><path d="M6.6 10.8a15.1 15.1 0 0 0 6.6 6.6l2.2-2.2c.3-.3.7-.4 1-.2 1.1.4 2.3.6 3.6.6.6 0 1 .4 1 1V20c0 .6-.4 1-1 1A17 17 0 0 1 3 4c0-.6.4-1 1-1h3.5c.6 0 1 .4 1 1 0 1.3.2 2.5.6 3.6.1.3 0 .7-.2 1l-2.3 2.2z"/></svg>
      </div>
      <div class="line">marcus@veltrowledger.com
        <svg class="icon" viewBox="0 0 24 24" aria-hidden="true"><path d="M2 5h20v14H2z"/><path d="M3 6l9 7 9-7" fill="none" stroke="#f6f6f6" stroke-width="1.6"/></svg>
      </div>
      <div class="line">www.veltrowledger.com
        <svg class="icon" viewBox="0 0 24 24" aria-hidden="true"><circle cx="12" cy="12" r="10"/><path d="M2 12h20M12 2c3 3 3 17 0 20M12 2c-3 3-3 17 0 20" fill="none" stroke="#f6f6f6" stroke-width="1.4"/></svg>
      </div>
    </div>
  </section>

</div>
</body>
</html>
```